Striking new Advert required for Commercial Real Estate Agency

We need a a NEW newspaper advertisement for the marketing of a large commercial property (a Backpackers lodge)

Dimensions are to be width of 101mm and height of 100mm (10cms)

Our key design statement for this advert is clean, modern and minimalist design, with accents of 'HOT PINK' colour to remove it from looking too boring, perhaps in the area of the contact icons. The heirachy of the advert is outlined in the attached ADVERTISEMENT TEXT FILE.

Our company name is THE HARBOURLINE COLLECTIVE, and we want our brand to appear professional yet classy in it's design style (sort of like an advertising or design agency)

We have two logo options below, one more square in its layout (which we prefer) and the other more rectangular, which may be better suited for the layout. We are not adverse to the logo being reversed (white text on black), along with other key element areas such as the main advert heading and the "FOR SALE" part, and think this would be a good option.
There are two photos attached to be included in the advert.

We have attached an example of an old advert that we did, which we DID NOT LIKE, and which was for a smaller width than the one we need (it is only 65% of the width of this one). WE have also atached a file showing layout of some of our competitors adverts, which we dont think are too good either.

We are really open for ideas, but have time pressures, so please come back with any questions as soon as you can, if needed.

Thank you
Updates

Thank you for the great and diverse designs. There are a few standout options, but one style that we prefer most.

Target Market(s)

We are wanting this newspaper advertisement to attract interest from real estat e developers, investors and motel/lodge owners, along with other high nett worth individuals

Industry/Entity Type

Real Estate

Font styles to use
Serif
Sans Serif

Colors
1b1b1b
a54499
474747
fbfbfb

Requirements
Must have
• Clean modern look, predominantly monochromatic or black and white, with the hot pink accent somewhere, as mentioned above.
• All the contents of the TEXT provided, perhaps with additional space to add a little more if needed, Please advise if you think we dont have enough space for all of the TEXT
Should not have
• Script like fonts
• Cartoonish characters
• a 'cheap' look

```html
<!DOCTYPE html>
<html lang="en">
<head>
<meta charset="utf-8">
<title>For Sale – Mount Victoria Land Grab</title>
<link href="https://fonts.googleapis.com/css2?family=Montserrat:wght@500;600;700&family=Roboto+Condensed:wght@300;400;700&display=swap" rel="stylesheet">
<style>
  :root{
    --ink:#1b1b1b;
    --band:#242122;
    --pink:#a54499;
    --grey:#474747;
    --paper:#fbfbfb;
    --white:#ffffff;
    --stage:#e9e9e9;
  }
  *{box-sizing:border-box;margin:0;padding:0}
  html,body{width:1200px;height:1000px;overflow:hidden;background:var(--stage)}
  .advert{position:absolute;left:160px;top:67px;width:880px;height:870px;background:var(--paper);overflow:hidden}
  .sale-strip{position:absolute;left:0;top:0;width:120px;height:473px;background:var(--ink)}
  .sale-strip span{position:absolute;left:60px;top:236px;transform:translate(-50%,-50%) rotate(-90deg);
    font-family:"Montserrat",sans-serif;font-weight:600;font-size:82px;letter-spacing:4px;color:var(--white);white-space:nowrap}
  .hero-photo{position:absolute;left:120px;top:0;width:760px;height:473px;
    background:linear-gradient(180deg,#8f9a86 0%,#b9bdb3 35%,#9c9a92 65%,#6f7a5e 100%)}
  .inset-photo{position:absolute;left:554px;top:260px;width:326px;height:213px;border-left:4px solid var(--white);border-top:4px solid var(--white);
    background:linear-gradient(180deg,#6f9ad6 0%,#b7c7d8 45%,#d9d8d2 65%,#5d7144 100%)}
  .title-band{position:absolute;left:0;top:473px;width:880px;height:62px;background:var(--band);text-align:right;padding:8px 36px 0 0;color:var(--white);font-family:"Montserrat",sans-serif}
  .title-band h1{font-size:19px;font-weight:600;letter-spacing:.3px}
  .title-band p{font-size:16.5px;font-weight:500;margin-top:1px}
  .details{position:absolute;left:28px;top:541px;width:830px;font-family:"Roboto Condensed",sans-serif;font-weight:300;color:var(--ink);font-size:21.5px;line-height:27px}
  .details ul{list-style:none}
  .details li{position:relative;padding-left:17px}
  .details li::before{content:"";position:absolute;left:2px;top:8px;width:9px;height:9px;background:var(--pink)}
  .tender{position:absolute;left:28px;top:739px;font-family:"Roboto Condensed",sans-serif;font-weight:700;font-size:21px;color:var(--pink)}
  .contact-bar{position:absolute;left:0;top:768px;width:880px;height:102px;background:var(--band);color:var(--white);font-family:"Roboto Condensed",sans-serif;font-weight:700}
  .contact-lines{position:absolute;left:28px;top:12px;font-size:19px;line-height:29px}
  .contact-lines .phones{display:flex;align-items:center;gap:6px;font-size:20px}
  .contact-lines svg{flex:none}
  .contact-lines .gap{width:10px}
  .brand{position:absolute;right:36px;top:0;height:102px;display:flex;align-items:center}
  .brand-name{font-family:"Montserrat",sans-serif;font-weight:500;font-size:18px;letter-spacing:1px;color:var(--white);white-space:nowrap}
</style>
</head>
<body>
<main class="advert">
  <div class="sale-strip"><span>FOR SALE</span></div>
  <div class="hero-photo" role="img" aria-label="Aerial view of the lodge buildings and car park among hillside suburb houses"></div>
  <div class="inset-photo" role="img" aria-label="Street-level view of the two-storey white weatherboard lodge with fire escape"></div>

  <header class="title-band">
    <h1>MOUNT VICTORIA LAND GRAB</h1>
    <p>Hilltop Lodge, 42 Alderley Street, Mount Victoria</p>
  </header>

  <section class="details">
    <p>This Old Beauty has served many, and is now ripe for development.</p>
    <p>One of Mt Vic’s largest land areas, now offered with vacant possession, with key details being:</p>
    <ul>
      <li>Large Land area of 2076m² with elevated sunny position and great outlook + access from Fernhill Street</li>
      <li>Existing Backpackers Lodge of 970m² providing multiple rooms with amenity areas</li>
      <li>Four adjacent sites also available, taking total land area to 4452m², an unprecedented Land Offering in this popular city fringe location</li>
    </ul>
  </section>
  <p class="tender">Now Selling by Closed Tender</p>

  <footer class="contact-bar">
    <div class="contact-lines">
      <p>Contact the Sole Agent : Miles Corrigan</p>
      <p class="phones">
        <svg width="18" height="18" viewBox="0 0 24 24" aria-hidden="true"><path fill="#a54499" d="M6.6 10.8a15.1 15.1 0 0 0 6.6 6.6l2.2-2.2c.3-.3.7-.4 1-.2 1.1.4 2.3.6 3.6.6.6 0 1 .4 1 1V20c0 .6-.4 1-1 1A17 17 0 0 1 3 4c0-.6.4-1 1-1h3.5c.6 0 1 .4 1 1 0 1.3.2 2.5.6 3.6.1.3 0 .7-.2 1z"/></svg>
        <span>(04) 555 0142</span><span class="gap"></span>
        <svg width="14" height="22" viewBox="0 0 14 22" aria-hidden="true"><rect x="1.5" y="1.5" width="11" height="19" rx="2" fill="none" stroke="#a54499" stroke-width="2"/><circle cx="7" cy="17" r="1.2" fill="#a54499"/></svg>
        <span>(021) 555 718</span>
      </p>
      <p>miles@harbourline.example &nbsp;|&nbsp; www.harbourline.example</p>
    </div>
    <div class="brand">
      <p class="brand-name">THE HARBOURLINE COLLECTIVE</p>
    </div>
  </footer>
</main>
</body>
</html>
```